MintVela business cards

We want to create two sets of cards. One general card for mintvela [staff] and one card for the founder of the company. Below is the general/basic information for you to format/display on side of the cards:
--Company address: 418 Larkmoor Street, New York, NY 10087
--Main phone: 212-736-5182
Will also provide you with secondary 1-800 number
--company website: www.mintvela.example
--email address for general card: frontdesk@mintvela.example
--email address (for dr hollings's card: md@mintvela.example
--titles for dr hollings's card: Founder, Medical Director
--Dr. Hollings's name on the card should read: Gregor T. Hollings, MD
You can also play around with mintvela's tag line: Quiet Glow Keeps Its Promise (TM or R should be attached as a trademark has been filed)
Reason: More time to design something awesome. This company is an aesthetic medical company that offers cool and safe cosmetic treatments
For the business card design for the doctor, please change the doctor's name to look like this above his title: Gregor T. Hollings, MD instead of using Dr. Gregor....etc
Reason: WILL NOT BE ABLE TO VIEW AND FINALIZE DESIGNS UNTIL I RETURN FROM MEDICAL CONFERENCE, WHICH WILL BE ON SUNDAY/MONDAY. MY APOLOGIES
can everyone try making it very minimalistic
A Bit of a change...
Can everyone take a stab at using a grey "raw" or eco friendly stock paper. We are interested to see the designs you come up with.
Business

```html
<!DOCTYPE html>
<html lang="en">
<head>
<meta charset="utf-8">
<title>MintVela business cards</title>
<link rel="stylesheet" href="https://fonts.googleapis.com/css2?family=Roboto+Condensed:wght@300;400;500&display=swap">
<style>
  :root {
    --sheet-edge: #58585a;
    --paper: #ffffff;
    --card-line: #222222;
    --ink: #4a4a4a;
    --brand-blue: #2a6db5;
    --sky-light: #d3e9f8;
    --sky-mid: #4ab8e8;
    --sky-deep: #2767b4;
  }
  * { box-sizing: border-box; margin: 0; padding: 0; }
  html, body { width: 1200px; height: 1200px; overflow: hidden; }
  body {
    background: var(--sheet-edge);
    font-family: "Roboto Condensed", "Arial Narrow", sans-serif;
    color: var(--ink);
  }
  .sheet {
    position: absolute;
    left: 16px; top: 16px;
    width: 1168px; height: 1168px;
    background: var(--paper);
  }
  .card {
    position: absolute;
    width: 494px; height: 282px;
    border: 1px solid var(--card-line);
    background: var(--paper);
    overflow: hidden;
  }
  .card--founder { left: 54px;  top: 274px; }
  .card--general { left: 615px; top: 274px; }
  .card--back-a  { left: 54px;  top: 616px; }
  .card--back-b  { left: 615px; top: 616px; }

  .side-band {
    position: absolute;
    left: 1px; top: 16px;
    width: 53px; height: 250px;
    background: linear-gradient(to bottom, var(--sky-light), var(--sky-mid) 45%, var(--sky-deep));
  }
  .side-band__url {
    position: absolute;
    left: 50%; top: 50%;
    transform: translate(-50%, -50%) rotate(-90deg);
    white-space: nowrap;
    color: #fff;
    font-size: 20px;
    font-weight: 400;
  }
  .details {
    position: absolute;
    left: 77px;
    font-size: 17px;
    font-weight: 300;
    line-height: 20px;
    white-space: nowrap;
  }
  .details p { margin: 0; }
  .details .gap { margin-top: 24px; }
  .details .gap-sm { margin-top: 4px; }
  .person__name {
    color: var(--brand-blue);
    font-size: 27px;
    font-weight: 500;
    line-height: 30px;
  }
  .person__title {
    font-size: 13px;
    font-weight: 400;
    line-height: 16px;
    margin-top: 2px;
    letter-spacing: 0.2px;
  }
  .card--founder .details { top: 37px; }
  .card--founder .details .gap-address { margin-top: 20px; }
  .card--general .details { top: 74px; }
  .card--general .details .gap { margin-top: 26px; }
  .card--general .details .gap-email { margin-top: 18px; }

  .wordmark {
    position: absolute;
    text-align: left;
    line-height: 1;
    white-space: nowrap;
  }
  .wordmark__name {
    display: block;
    font-weight: 400;
    letter-spacing: -0.5px;
  }
  .wordmark__tagline {
    display: block;
    text-transform: uppercase;
    font-weight: 400;
  }
  .wordmark--small { left: 304px; }
  .wordmark--small .wordmark__name { font-size: 50px; color: var(--brand-blue); }
  .wordmark--small .wordmark__tagline { font-size: 6px; letter-spacing: 1.6px; color: var(--brand-blue); margin-top: 1px; }
  .card--founder .wordmark--small { top: 186px; }
  .card--general .wordmark--small { top: 166px; left: 296px; }

  .back-panel {
    position: absolute;
    left: 17px; top: 15px;
    width: 477px; height: 250px;
    background: linear-gradient(to bottom, var(--sky-light), var(--sky-mid) 48%, var(--sky-deep));
  }
  .wordmark--large {
    left: 50%; top: 50%;
    transform: translate(-50%, -52%);
  }
  .wordmark--large .wordmark__name { font-size: 96px; color: #fff; font-weight: 300; }
  .wordmark--large .wordmark__tagline { font-size: 11px; letter-spacing: 3px; color: #fff; margin-top: 2px; }
</style>
</head>
<body>
  <main class="sheet">
    <section class="card card--founder" aria-label="Founder card, front">
      <div class="side-band"><span class="side-band__url">www.mintvela.example</span></div>
      <div class="details">
        <p class="person__name">Gregor T. Hollings, MD</p>
        <p class="person__title">FOUNDER, MEDICAL DIRECTOR</p>
        <p class="gap-address">418 Larkmoor Street</p>
        <p>New York, NY 10087</p>
        <p class="gap">212.736.5182</p>
        <p class="gap-sm">1.800.000.0000</p>
        <p class="gap-sm">md@mintvela.example</p>
      </div>
      <div class="wordmark wordmark--small">
        <span class="wordmark__name">mintvela</span>
        <span class="wordmark__tagline">Quiet Glow Keeps Its Promise™</span>
      </div>
    </section>

    <section class="card card--general" aria-label="General staff card, front">
      <div class="side-band"><span class="side-band__url">www.mintvela.example</span></div>
      <div class="details">
        <p>418 Larkmoor Street</p>
        <p>New York, NY 10087</p>
        <p class="gap">212.736.5182</p>
        <p class="gap-sm">1.800.000.0000</p>
        <p class="gap-email">frontdesk@mintvela.example</p>
      </div>
      <div class="wordmark wordmark--small">
        <span class="wordmark__name">mintvela</span>
        <span class="wordmark__tagline">Quiet Glow Keeps Its Promise™</span>
      </div>
    </section>

    <section class="card card--back-a" aria-label="Card back">
      <div class="back-panel">
        <div class="wordmark wordmark--large">
          <span class="wordmark__name">mintvela</span>
          <span class="wordmark__tagline">Quiet Glow Keeps Its Promise™</span>
        </div>
      </div>
    </section>

    <section class="card card--back-b" aria-label="Card back">
      <div class="back-panel">
        <div class="wordmark wordmark--large">
          <span class="wordmark__name">mintvela</span>
          <span class="wordmark__tagline">Quiet Glow Keeps Its Promise™</span>
        </div>
      </div>
    </section>
  </main>
</body>
</html>
```